Kelvaro.ch is looking for business card letterhead and envelope C5 with WOW effect

We need a strong business card for our company Kelvaro.ch, logo is available. You want a black or dark background on which the logo Stark r% 26 # 252; appears. Letterhead and envelope in C5 format should be in a similar design, but does not have to be We need a strong business card for our company Kelvaro.ch, logo is available. A black or dark background is desired, on which the logo Stark comes across. The letterhead and the envelope in C5 format should have a similar design.

Target Market(s)

Private customers as well as entrepreneurs

Contact Information for Business Card

E-mail: info@kelvaro-example.ch
Web.www.Kelvaro-example.ch
Tel: +41 ( 0 ) 79 482 6037
Adresse:
Lindenweg 14
9406 Tarnbach

Hier kann man Icons verwenden für Email,Tel und Adressse

Font styles to use
Other font styles liked:
• Dubai,bold

Colors

Designer to choose colors to be used in the design.

Requirements
Must have
• WOW effect
Nice to have
• R% 26 # 252; back business card with our service listings. - VEHICLE LABELING - SHOP WINDOW LABELING - STICKERS AND MUCH MORE ... in red color

```html
<!DOCTYPE html>
<html lang="en">
<head>
<meta charset="utf-8">
<title>Kelvaro.ch Business Card</title>
<link href="https://fonts.googleapis.com/css2?family=Montserrat:wght@700;800&family=Open+Sans:wght@400;600&display=swap" rel="stylesheet">
<style>
  :root {
    --backdrop: #e9e7e3;
    --navy: #15203f;
    --navy-deep: #0f1833;
    --white: #ffffff;
    --honey: #f7c51a;
    --signal-red: #d41f26;
    --muted: #d9dde8;
  }
  * { margin: 0; padding: 0; box-sizing: border-box; }
  html, body {
    width: 1200px; height: 930px; overflow: hidden;
    background: var(--backdrop);
  }
  .canvas { position: relative; width: 1200px; height: 930px; }
  .card {
    position: absolute; width: 620px; height: 360px;
    border-radius: 22px; overflow: hidden;
    background: linear-gradient(135deg, #1c2850 0%, var(--navy) 45%, var(--navy-deep) 100%);
    box-shadow: 0 14px 30px rgba(0,0,0,0.25);
    color: var(--white);
  }
  .card--front { left: 90px; top: 70px; }
  .card--back { left: 490px; top: 500px; }

  .wordmark {
    font-family: "Montserrat", sans-serif; font-weight: 800;
    color: var(--white); letter-spacing: 1px; text-transform: uppercase;
    position: absolute; white-space: nowrap;
  }

  /* front */
  .card--front .honeycomb {
    position: absolute; left: 70px; top: 95px; width: 200px; height: 150px;
    background: radial-gradient(circle at 40% 50%, #f9cf2c 0%, #e9b612 70%, rgba(233,182,18,0.0) 100%);
    border-radius: 16px;
  }
  .card--front .wordmark { left: 290px; top: 110px; font-size: 40px; }
  .services {
    position: absolute; left: 290px; top: 175px;
    font-family: "Open Sans", sans-serif; font-size: 14px; font-weight: 400;
    letter-spacing: 0.4px; text-transform: uppercase; color: var(--white);
    list-style: none; line-height: 1.9;
  }
  .services li::before {
    content: ""; display: inline-block; width: 7px; height: 7px;
    border-radius: 50%; background: var(--signal-red);
    margin-right: 8px; vertical-align: middle;
  }

  /* back */
  .card--back .wordmark { left: 0; right: 0; text-align: center; top: 36px; font-size: 34px; }
  .holder {
    position: absolute; left: 0; right: 0; top: 105px; text-align: center;
  }
  .holder__name {
    font-family: "Montserrat", sans-serif; font-weight: 800;
    font-size: 24px; letter-spacing: 2px; text-transform: uppercase;
  }
  .holder__surname { color: var(--honey); }
  .holder__role {
    font-family: "Open Sans", sans-serif; font-size: 14px; color: var(--muted); margin-top: 2px;
  }
  .contact-icons {
    position: absolute; left: 0; right: 0; top: 170px;
    display: flex; justify-content: center; gap: 8px;
  }
  .contact-icons svg { width: 24px; height: 24px; }
  .contact-lines {
    position: absolute; left: 0; right: 0; top: 202px; text-align: center;
    font-family: "Open Sans", sans-serif; font-size: 15px; line-height: 1.45; color: var(--white);
  }
  .address {
    position: absolute; left: 0; right: 0; top: 286px; text-align: center;
    font-family: "Open Sans", sans-serif; font-size: 15px; color: var(--white);
  }
  .address svg { width: 14px; height: 14px; vertical-align: -2px; margin-right: 6px; }
  .card--back .honeycomb {
    position: absolute; left: 0; bottom: 0; width: 210px; height: 170px;
    background: radial-gradient(circle at 35% 65%, #f9cf2c 0%, #e9b612 65%, rgba(233,182,18,0.0) 100%);
    border-radius: 0 60px 0 0;
  }
</style>
</head>
<body>
<main class="canvas">

  <section class="card card--front" aria-label="Business card front">
    <div class="honeycomb" role="img" aria-label="Yellow honeycomb cluster of hexagons"></div>
    <div class="wordmark">Kelvaro.ch</div>
    <ul class="services">
      <li>Stickers and much more</li>
      <li>Shop window labeling</li>
      <li>Vehicle labeling</li>
    </ul>
  </section>

  <section class="card card--back" aria-label="Business card back">
    <div class="wordmark">Kelvaro.ch</div>
    <div class="holder">
      <div class="holder__name">Lukas <span class="holder__surname">Brenner</span></div>
      <div class="holder__role">Director</div>
    </div>
    <div class="contact-icons">
      <svg viewBox="0 0 24 24" aria-label="Phone">
        <circle cx="12" cy="12" r="10.5" fill="none" stroke="var(--honey)" stroke-width="1.6"/>
        <path d="M8.5 7.5c.6-.6 1.3-.5 1.7.1l.8 1.3c.3.5.2 1-.2 1.4l-.6.5c.5 1.2 1.4 2.1 2.6 2.6l.5-.6c.4-.4.9-.5 1.4-.2l1.3.8c.6.4.7 1.1.1 1.7l-.6.6c-.7.7-3 .3-5-1.7s-2.4-4.3-1.7-5z" fill="var(--honey)"/>
      </svg>
      <svg viewBox="0 0 24 24" aria-label="Email">
        <circle cx="12" cy="12" r="10.5" fill="none" stroke="var(--honey)" stroke-width="1.6"/>
        <rect x="6.5" y="8" width="11" height="8" rx="1" fill="none" stroke="var(--honey)" stroke-width="1.5"/>
        <path d="M6.8 8.5 12 12.5l5.2-4" fill="none" stroke="var(--honey)" stroke-width="1.5"/>
      </svg>
      <svg viewBox="0 0 24 24" aria-label="Website">
        <circle cx="12" cy="12" r="10.5" fill="none" stroke="var(--honey)" stroke-width="1.6"/>
        <circle cx="12" cy="12" r="6" fill="none" stroke="var(--honey)" stroke-width="1.3"/>
        <ellipse cx="12" cy="12" rx="2.6" ry="6" fill="none" stroke="var(--honey)" stroke-width="1.2"/>
        <path d="M6 12h12M7 9h10M7 15h10" stroke="var(--honey)" stroke-width="1.1"/>
      </svg>
    </div>
    <div class="contact-lines">
      <div>+41 ( 0 ) 79 482 6037</div>
      <div>info@kelvaro-example.ch</div>
      <div>www.Kelvaro-example.ch</div>
    </div>
    <div class="address">
      <svg viewBox="0 0 14 14" aria-hidden="true"><polygon points="7,1 12.2,4 12.2,10 7,13 1.8,10 1.8,4" fill="none" stroke="var(--honey)" stroke-width="2"/></svg>Lindenweg 14, 9406 Tarnbach
    </div>
    <div class="honeycomb" role="img" aria-label="Yellow honeycomb cluster of hexagons in the corner"></div>
  </section>

</main>
</body>
</html>
```